Fizz's Shed & Grill Burger Restaurant Website - HomePage Only PSD

I need a website design for a restaurant called "Fizz's Shed and Grill" featuring burgers, wings, beer, live music, trivia, and more. I have several images of the restaurant and they already have their logo files created (see attached). I want some type of wood background and integrate the silver tin. This needs to be a modern, hip and fun type design. Design must incorporate these attached graphics.

UPDATE - just added a few more images of things I really like to be incorporated into my designs.
Updates

Industry/Entity Type

Burger Restaurant

Number of Pages Required

1 page

Font styles to use
Sans Serif

Requirements
Must have
• Restaurant/Bar theme with integration of existing logo and the red wood look.
Nice to have
• - Modern Fun appearance
• - Use Pelko Fonts

```html
<!DOCTYPE html>
<html lang="en">
<head>
<meta charset="utf-8">
<title>Fizz's Shed and Grill</title>
<link rel="stylesheet" href="https://fonts.googleapis.com/css2?family=Oswald:wght@400;500&family=Roboto:wght@400;500&display=swap">
<style>
:root{
  --red:#d0201f;
  --red-dark:#a51615;
  --nav:#2b2320;
  --wood-1:#5a2e17;
  --wood-2:#7a4222;
  --wood-seam:#3a1c0d;
  --card:#f4f4f4;
  --ink:#333333;
  --muted:#555555;
  --white:#ffffff;
  --footer:#1a1a1a;
  --dusk-1:#1f2a36;
  --dusk-2:#3a3530;
}
*{box-sizing:border-box;margin:0;padding:0}
html,body{width:1200px;height:2270px;overflow:hidden}
body{font-family:"Roboto",Arial,sans-serif;color:var(--white);position:relative;background:var(--footer)}
.section{position:absolute;left:0;width:1200px}
.wood{
  background:
    repeating-linear-gradient(90deg,transparent 0 62px,var(--wood-seam) 62px 65px),
    linear-gradient(180deg,var(--wood-2),var(--wood-1) 50%,var(--wood-2));
}
/* hero */
.hero{top:0;height:676px}
.hero-photo{position:absolute;inset:0;background:linear-gradient(180deg,#8a3a32 0%,#b9aa96 22%,#d7cfc2 45%,#6f6a52 72%,#8f7c62 100%)}
.topbar{position:absolute;top:0;left:0;width:1200px;height:90px;background:linear-gradient(180deg,rgba(30,24,22,.92),rgba(60,40,34,.75))}
.nav-link{position:absolute;top:26px;height:42px;line-height:42px;font-size:15px;color:var(--white);text-transform:uppercase;letter-spacing:.3px}
.nav-link.active{background:var(--red);padding:0 16px;border-radius:2px}
.brand{position:absolute;left:542px;top:7px;width:116px;height:116px;border-radius:50%;background:var(--white);border:3px solid #222;display:flex;align-items:center;justify-content:center;text-align:center;color:#222;font-size:16px;font-weight:500;line-height:1.2;padding:10px}
.hero-band{position:absolute;left:0;top:481px;width:590px;height:160px;background:rgba(190,30,30,.55)}
.hero-title{position:absolute;left:82px;top:490px;font-family:"Oswald",Arial,sans-serif;font-size:56px;font-weight:400;line-height:68px;text-transform:uppercase}
.hero-sub{position:absolute;left:84px;top:558px;font-size:24px;line-height:34px;width:500px}
.slider-arrow{position:absolute;top:601px;width:33px;height:42px;background:rgba(40,40,40,.8);display:flex;align-items:center;justify-content:center}
/* restaurant */
.restaurant{top:676px;height:504px}
.section-title{position:absolute;left:0;width:1200px;text-align:center;font-family:"Oswald",Arial,sans-serif;font-size:38px;font-weight:400;text-transform:uppercase}
.feature-card{position:absolute;top:191px;width:248px;height:256px;background:linear-gradient(180deg,var(--white),var(--card));border-radius:5px;box-shadow:0 2px 6px rgba(0,0,0,.45);text-align:center;color:var(--ink)}
.feature-photo{position:absolute;top:122px;width:146px;height:146px;border-radius:50%;border:4px solid var(--white);box-shadow:0 2px 6px rgba(0,0,0,.4)}
.feature-name{margin-top:88px;font-size:25px;font-weight:400;color:var(--ink)}
.feature-text{margin:12px auto 0;width:210px;font-size:12px;line-height:21px;color:var(--muted)}
.read-more{display:block;margin-top:12px;font-size:12px;color:var(--red)}
/* welcome */
.welcome{top:1180px;height:472px;background:linear-gradient(180deg,var(--dusk-1),var(--dusk-2) 60%,#2a221c)}
.welcome-title{position:absolute;left:86px;top:106px;font-family:"Oswald",Arial,sans-serif;font-size:33px;font-weight:400;text-transform:uppercase}
.welcome-text{position:absolute;left:86px;top:156px;width:575px;font-size:15px;line-height:24.5px}
.btn{position:absolute;left:86px;top:329px;width:148px;height:53px;background:var(--red);border-radius:3px;font-size:18px;line-height:53px;text-align:center;box-shadow:0 2px 4px rgba(0,0,0,.5)}
.welcome-art{position:absolute;left:748px;top:75px;width:326px;height:326px;border-radius:50%;border:12px solid rgba(208,80,80,.75);background:linear-gradient(135deg,#7c8ea0,#c9a27d 50%,#586877)}
/* blog */
.blog{top:1652px;height:482px}
.post{position:absolute;top:123px;width:314px}
.post-photo{width:314px;height:189px;border:3px solid var(--white);position:relative}
.post-date{position:absolute;right:0;top:45px;width:50px;text-align:center;font-size:20px}
.post-date .day{display:block;background:var(--red);padding-top:8px;line-height:22px}
.post-date .mon{display:block;background:var(--red);font-size:11px;padding-bottom:8px}
.post-date .yr{display:block;background:#1b1b1b;font-size:15px;line-height:38px}
.post-title{margin-top:22px;font-size:16px}
.post-text{margin-top:8px;font-size:11.5px;line-height:17px}
/* footer */
.footer{top:2134px;height:136px;background:var(--footer)}
.footer-links{position:absolute;left:92px;top:44px;font-size:12.5px}
.copyright{position:absolute;left:92px;top:69px;font-size:12.5px}
.social{position:absolute;top:45px;width:36px;height:36px;border-radius:50%;border:2px solid var(--white)}
</style>
</head>
<body>

<header class="section hero">
  <div class="hero-photo" role="img" aria-label="Photo of the restaurant front with a longhorn statue and red metal roof"></div>
  <nav class="topbar">
    <span class="nav-link active" style="left:92px">Home</span>
    <span class="nav-link" style="left:201px">About Us</span>
    <span class="nav-link" style="left:324px">Products</span>
    <span class="nav-link" style="left:452px">Menu</span>
    <span class="nav-link" style="left:705px">Gallary</span>
    <span class="nav-link" style="left:821px">Event</span>
    <span class="nav-link" style="left:920px">Press</span>
    <span class="nav-link" style="left:1017px">Contact Us</span>
  </nav>
  <div class="brand">Fizz's Shed and Grill</div>
  <div class="hero-band"></div>
  <h1 class="hero-title">Fizz's Shed and Gril</h1>
  <p class="hero-sub">Neque porro quisquam est qui dolorem ipsum quia dolor sit amet consectetur,</p>
  <div class="slider-arrow" style="left:1059px"><svg width="12" height="20" viewBox="0 0 12 20"><path d="M10 2 2 10l8 8" fill="none" stroke="#fff" stroke-width="2"/></svg></div>
  <div class="slider-arrow" style="left:1094px"><svg width="12" height="20" viewBox="0 0 12 20"><path d="M2 2l8 8-8 8" fill="none" stroke="#fff" stroke-width="2"/></svg></div>
</header>

<section class="section restaurant wood">
  <h2 class="section-title" style="top:53px">Our Restaurant</h2>

  <article class="feature-card" style="left:85px">
    <p class="feature-name">Burgers</p>
    <p class="feature-text">Lorem Ipsum has been the industry's standard dummy text ever since the 1500s, when an unknown printer took</p>
    <span class="read-more">ReadMore »</span>
  </article>
  <article class="feature-card" style="left:345px">
    <p class="feature-name">Wings</p>
    <p class="feature-text">Lorem Ipsum has been the industry's standard dummy text ever since the 1500s, when an unknown printer took</p>
    <span class="read-more">ReadMore »</span>
  </article>
  <article class="feature-card" style="left:602px">
    <p class="feature-name">Beer</p>
    <p class="feature-text">Lorem Ipsum has been the industry's standard dummy text ever since the 1500s, when an unknown printer took</p>
    <span class="read-more">ReadMore »</span>
  </article>
  <article class="feature-card" style="left:864px">
    <p class="feature-name">Live music</p>
    <p class="feature-text">Lorem Ipsum has been the industry's standard dummy text ever since the 1500s, when an unknown printer took</p>
    <span class="read-more">ReadMore »</span>
  </article>

  <div class="feature-photo" style="left:136px;background:radial-gradient(circle,#c9762e,#6b3a1c)" role="img" aria-label="Burger photo"></div>
  <div class="feature-photo" style="left:396px;background:radial-gradient(circle,#d0612a,#7a2f14)" role="img" aria-label="Chicken wings photo"></div>
  <div class="feature-photo" style="left:653px;background:radial-gradient(circle,#e3a23a,#5a3416)" role="img" aria-label="Glass of beer photo"></div>
  <div class="feature-photo" style="left:915px;background:radial-gradient(circle,#6b5a44,#1c1712)" role="img" aria-label="Drum kit on stage photo"></div>
</section>

<section class="section welcome" role="img" aria-label="Dusk view of the restaurant patio with tin fence">
  <h2 class="welcome-title">Welcome to Fizz's Shed and Grill</h2>
  <p class="welcome-text">Lorem Ipsum has been the industry's standard dummy text ever since the 1500s, when an unknown printer took a galley of type and scrambled it to make a type specimen book. It has survived not only five centuries, but also the leap into electronic typesetting, remaining essentially unchanged. It was popularised in the 1960s with the release of Letraset sheets containing Lorem Ipsum passages, and more recently with desktop publishing software like Aldus PageMaker including versions of Lorem Ipsum</p>
  <span class="btn">View More</span>
  <div class="welcome-art" role="img" aria-label="Colourful painted artwork in a round frame"></div>
</section>

<section class="section blog wood">
  <h2 class="section-title" style="top:40px">Latest Blog</h2>

  <article class="post" style="left:92px">
    <div class="post-photo" style="background:linear-gradient(135deg,#6e4a2c,#b9b06a 50%,#3b2a1c)" role="img" aria-label="Restaurant name sign on wood wall">
      <div class="post-date"><span class="day">02</span><span class="mon">JUN</span><span class="yr">2016</span></div>
    </div>
    <p class="post-title">Lorem ipsum dolor sit amet,</p>
    <p class="post-text">Lorem ipsum dolor sit amet, consectetur adipiscing elit. Sed blandit massa vel mauris sollicitudin dignissim. Lorem ipsum dolor sit amet, consectetur</p>
  </article>
  <article class="post" style="left:445px">
    <div class="post-photo" style="background:linear-gradient(135deg,#8a8f94,#d5d8da 50%,#7a7f84)" role="img" aria-label="Metal sign mounted on silver tin wall">
      <div class="post-date"><span class="day">02</span><span class="mon">JUN</span><span class="yr">2016</span></div>
    </div>
    <p class="post-title">Lorem ipsum dolor sit amet,</p>
    <p class="post-text">Lorem ipsum dolor sit amet, consectetur adipiscing elit. Sed blandit massa vel mauris sollicitudin dignissim. Lorem ipsum dolor sit amet, consectetur</p>
  </article>
  <article class="post" style="left:797px">
    <div class="post-photo" style="background:linear-gradient(135deg,#6d6a60,#b8623a 50%,#5a5a52)" role="img" aria-label="Painted canvas hanging on restaurant wall">
      <div class="post-date"><span class="day">02</span><span class="mon">JUN</span><span class="yr">2016</span></div>
    </div>
    <p class="post-title">Lorem ipsum dolor sit amet,</p>
    <p class="post-text">Lorem ipsum dolor sit amet, consectetur adipiscing elit. Sed blandit massa vel mauris sollicitudin dignissim. Lorem ipsum dolor sit amet, consectetur</p>
  </article>
</section>

<footer class="section footer">
  <p class="footer-links">Privacy Policy | Terms of Use | About Us | Sitemap</p>
  <p class="copyright">Copyright © 2016 All rights reserved.</p>
  <span class="social" style="left:912px;background:#3b5998" aria-label="Social link"></span>
  <span class="social" style="left:965px;background:#1da1f2" aria-label="Social link"></span>
  <span class="social" style="left:1018px;background:#dd4b39" aria-label="Social link"></span>
  <span class="social" style="left:1068px;background:#0e76a8" aria-label="Social link"></span>
</footer>

</body>
</html>
```